Lantern Petals Website v.1 - attract floral shop franchisees

I need a simple information website for my new business. We are a franchisor of flower shops. The overall purpose of the website is to promote the company and the service, especially to potential franchisees and retailers. Only about 4 pages are required including homepage, About, For Supermarkets, For Franchisees, and Contact. No special functions are required except the site will have two separate inquiry forms that must be filled out online and submitted via automated email. Similarly, an email form should be linked from the Contact page. I have a logo and business cards designed by ArtMingle, and I would like the site to have a consistent color scheme and style. The key to design will be to express the joy and love associated with flowers and floral bouquets.
IMPORTANT - I will be exporting the website design to Wordpress CMS in a site hosted by HostNimbus. For smooth integration into WordPress hosted by HostNimbus, the designer should build the site using a WordPress-friendly format. Ideally, they should use HTML, CSS, and PHP. Creating a custom theme or using a page builder that exports to WordPress-compatible files is best. This ensures the site can be easily imported and managed within WordPress.

Target Market(s)

Potential franchisees (existing florists or creative types who might like to own a floral business) and supermarkets who might want us to run their floral department

Industry/Entity Type

Floral retailing

Requirements
Must have
• A brand theme that is beautiful, consistent throughout and builds on the logo design
Nice to have
• Show gender and ethnic diversity in customers and florists. Pictures of happy florists (for franchisees) and pictures of amazing floral department displays (for supermarkets)

```html
<!DOCTYPE html>
<html lang="en">
<head>
<meta charset="utf-8">
<title>Lantern Petals – Contact</title>
<link rel="stylesheet" href="https://fonts.googleapis.com/css2?family=Libre+Baskerville:wght@400;700&family=Poppins:wght@400;500;700&display=swap">
<style>
:root{
  --amber:#f2ae2e;
  --green:#04773f;
  --ink:#111111;
  --field:#ececee;
  --muted:#666666;
  --line:#d9d9d9;
  --link:#2f4fb8;
  --white:#ffffff;
}
*{box-sizing:border-box;margin:0;padding:0}
html,body{width:861px;height:1200px;overflow:hidden;background:var(--white)}
body{position:relative;font-family:'Poppins',sans-serif;color:var(--ink)}
.abs{position:absolute}
.serif{font-family:'Libre Baskerville',serif}

.site-header{left:0;top:0;width:861px;height:64px;background:var(--white)}
.brand{left:77px;top:20px;display:flex;align-items:center;gap:6px;font-family:'Libre Baskerville',serif;font-size:14px;color:var(--amber)}
.brand-dot{width:18px;height:18px;border-radius:50%;background:var(--amber)}
.menu-toggle{left:752px;top:22px;width:25px}
.menu-toggle span{display:block;height:2px;background:var(--ink);margin-bottom:6px}

.hero{left:0;top:64px;width:861px;height:310px;background:radial-gradient(ellipse at 50% 55%,#d9c3a1 0%,#c9b08b 45%,#6a7b48 78%,#2f4a22 100%)}
.hero-name{left:0;top:250px;width:881px;text-align:center;font-weight:700;font-size:9px;letter-spacing:.3px}
.hero-mark{left:420px;top:185px;width:48px;height:48px;border-radius:50%;border:2px solid var(--amber)}
.hero-title{left:0;top:268px;width:881px;text-align:center;font-size:30px}

.intro-title{left:0;top:433px;width:861px;text-align:center;font-size:21px}
.intro-sub{left:0;top:460px;width:861px;text-align:center;font-size:9.2px;color:var(--muted)}

.label{font-family:'Libre Baskerville',serif;font-weight:700;font-size:10px}
.field{background:var(--field);font-size:8.5px;color:#777;padding-left:10px;display:flex;align-items:center}
.field.area{align-items:flex-start;padding:12px 16px}
.submit{left:84px;top:737px;width:374px;height:33px;background:var(--amber);color:var(--white);font-weight:700;font-size:11px;display:flex;align-items:center;justify-content:center}
.submit svg{position:absolute;right:13px;top:10px}

.info-icon{width:48px;height:48px;border-radius:50%;background:var(--amber);display:flex;align-items:center;justify-content:center}
.info-label{font-size:14px}
.info-value{font-size:16.5px}
.info-rule{left:563px;width:168px;height:1px;background:var(--line)}

.cta-band{left:77px;top:897px;width:701px;height:138px;background:var(--amber)}
.bouquet{left:118px;top:815px;width:252px;height:220px;border-radius:45% 45% 10% 10%;background:radial-gradient(ellipse at 50% 38%,#e07ab5 0%,#c34c9a 35%,#8fbf3a 65%,rgba(143,191,58,0) 72%)}
.cta-text{left:387px;top:944px;color:var(--white);font-weight:700;font-size:17px;line-height:19.5px}
.cta-text a{color:var(--link);text-decoration:underline}

.site-footer{left:0;top:1023px;width:861px;height:177px;background:var(--green)}
.footer-brand{left:0;top:1068px;width:861px;display:flex;justify-content:center;align-items:center;gap:8px;color:var(--white);font-family:'Libre Baskerville',serif;font-size:22px}
.footer-dot{width:26px;height:26px;border-radius:50%;border:2px solid var(--white)}
.social{top:1124px;width:22px;height:22px;border-radius:50%;background:rgba(255,255,255,.18)}
.footer-rule{left:133px;top:1170px;width:606px;height:1px;background:rgba(255,255,255,.2)}
.footer-small{top:1182px;font-size:7.5px;color:var(--white)}
</style>
</head>
<body>

<header class="abs site-header">
  <div class="abs brand"><span class="brand-dot"></span>Lantern Petals</div>
  <div class="abs menu-toggle"><span></span><span></span><span></span></div>
</header>

<section class="abs hero" role="img" aria-label="Florist workbench with kraft paper, ribbons, scissors and tropical flowers"></section>
<div class="abs hero-mark"></div>
<div class="abs hero-name">LANTERN PETALS</div>
<h1 class="abs hero-title serif">Contact</h1>

<h2 class="abs intro-title serif">Get In touch with us</h2>
<p class="abs intro-sub">For more information about becoming a franchisee with us, please reach out:</p>

<div class="abs label" style="left:85px;top:479px">Name</div>
<div class="abs field" style="left:84px;top:494px;width:375px;height:29px">Enter your name</div>
<div class="abs label" style="left:85px;top:534px">Email</div>
<div class="abs field" style="left:84px;top:549px;width:185px;height:29px">Enter your email</div>
<div class="abs label" style="left:274px;top:534px">Telephone</div>
<div class="abs field" style="left:274px;top:549px;width:185px;height:29px">Enter phone number</div>
<div class="abs label" style="left:85px;top:588px">Message</div>
<div class="abs field area" style="left:84px;top:603px;width:375px;height:121px">Type your text...</div>
<div class="abs submit">SUBMIT
  <svg width="13" height="12" viewBox="0 0 24 22"><path d="M23 1 1 10l7 3 2 8 4-6 6 4z" fill="#fff"/></svg>
</div>

<div class="abs info-icon" style="left:499px;top:521px">
  <svg width="18" height="18" viewBox="0 0 24 24"><path d="M6.6 10.8a15 15 0 0 0 6.6 6.6l2.2-2.2a1 1 0 0 1 1-.25 11 11 0 0 0 3.6.6 1 1 0 0 1 1 1V20a1 1 0 0 1-1 1A17 17 0 0 1 3 4a1 1 0 0 1 1-1h3.5a1 1 0 0 1 1 1c0 1.2.2 2.5.6 3.6a1 1 0 0 1-.25 1z" fill="#fff"/></svg>
</div>
<div class="abs info-label" style="left:561px;top:520px">Phone:</div>
<div class="abs info-value" style="left:561px;top:540px">(555) 014-2738</div>
<div class="abs info-rule" style="top:583px"></div>

<div class="abs info-icon" style="left:499px;top:601px">
  <svg width="17" height="13" viewBox="0 0 24 18"><rect width="24" height="18" rx="2" fill="#fff"/><path d="M1 2l11 8 11-8" stroke="#f2ae2e" stroke-width="2" fill="none"/></svg>
</div>
<div class="abs info-label" style="left:561px;top:600px">Email:</div>
<div class="abs info-value" style="left:561px;top:622px">info@lantern-petals.com</div>
<div class="abs info-rule" style="top:663px"></div>

<div class="abs info-icon" style="left:499px;top:681px">
  <svg width="15" height="20" viewBox="0 0 18 24"><path d="M9 0a9 9 0 0 0-9 9c0 7 9 15 9 15s9-8 9-15a9 9 0 0 0-9-9zm0 12.5A3.5 3.5 0 1 1 9 5.5a3.5 3.5 0 0 1 0 7z" fill="#fff"/></svg>
</div>
<div class="abs info-label" style="left:562px;top:682px">Address:</div>
<div class="abs" style="left:562px;top:704px;font-size:14.5px;line-height:22px">48 Petal Lane, Marigold<br>Springs, FL 30417</div>

<div class="abs cta-band"></div>
<div class="abs bouquet" role="img" aria-label="Bouquet of pink lilies, roses and green chrysanthemums in a glass vase"></div>
<p class="abs cta-text serif">For questions and further information,<br>contact <a href="mailto:info@lantern-petals.com">info@lantern-petals.com</a></p>

<footer class="abs site-footer"></footer>
<div class="abs footer-brand"><span class="footer-dot"></span>Lantern Petals</div>
<div class="abs social" style="left:381px"></div>
<div class="abs social" style="left:407px"></div>
<div class="abs social" style="left:434px"></div>
<div class="abs social" style="left:460px"></div>
<div class="abs footer-rule"></div>
<div class="abs footer-small" style="left:133px">© 2024 Lantern Petals, All rights reserved</div>
<div class="abs footer-small" style="left:589px">Terms &amp; conditions</div>
<div class="abs footer-small" style="left:687px">Privacy policy</div>

</body>
</html>
```